Brindovalle Business cards

Dear team, I need to get the design file to suit it to our team. The focus of the business card is the Automotive Market and the design must be in black colour and the logo must be in glossy black. On the front of the card I need to get the following info:

- Name and Surname
- Title
- eMail
- Phone Number
- Skype account
- domain address

```html
<!DOCTYPE html>
<html lang="en">
<head>
<meta charset="UTF-8">
<title>Brindovalle Business Card</title>
<link href="https://fonts.googleapis.com/css2?family=Archivo:ital,wght@0,400;0,800;1,400;1,800&display=swap" rel="stylesheet">
<style>
  :root {
    --backdrop: #2b2b2d;
    --card: #19191b;
    --red: #e8232e;
    --white: #f4f4f4;
    --sheen-dark: #111113;
    --sheen-mid: #2e2e31;
    --sheen-light: #55555a;
  }
  * { margin: 0; padding: 0; box-sizing: border-box; }
  html, body {
    width: 1200px; height: 900px; overflow: hidden;
    background: var(--backdrop);
    font-family: "Archivo", Arial, sans-serif;
  }
  .card {
    position: absolute; left: 250px;
    width: 700px; height: 400px;
    background: var(--card);
    border-radius: 20px;
    overflow: hidden;
    box-shadow: 0 16px 40px rgba(0,0,0,.5);
  }
  .card--front { top: 34px; }
  .card--back { top: 466px; }

  /* front */
  .card__band {
    position: absolute; left: 0; right: 0; bottom: 0;
    height: 13px; background: var(--red);
  }
  .brand {
    position: absolute; left: 210px; top: 66px;
    display: flex; align-items: center; gap: 14px;
  }
  .brand__mark { width: 28px; height: 28px; background: var(--red); flex: none; }
  .brand__name {
    color: var(--white); font-weight: 800; font-size: 44px;
    letter-spacing: -1px; line-height: 1;
  }
  .person {
    position: absolute; right: 372px; top: 200px; text-align: right;
  }
  .person__name {
    color: var(--red); font-weight: 800; font-style: italic;
    font-size: 29px; text-transform: uppercase; letter-spacing: .3px; line-height: 1.1;
  }
  .person__title {
    color: var(--white); font-style: italic; font-size: 18px; margin-top: 4px;
  }
  .divider {
    position: absolute; left: 344px; top: 180px;
    width: 3px; height: 126px; background: var(--red);
  }
  .contact {
    position: absolute; left: 374px; top: 180px;
    color: var(--white); font-size: 17px; line-height: 1.3;
    list-style: none;
  }
  .contact__address { margin-bottom: 10px; }
  .contact__item { display: flex; align-items: center; gap: 9px; }
  .contact__icon { width: 14px; height: 14px; flex: none; }

  /* back */
  .back__pattern {
    position: absolute; inset: 0;
    background:
      linear-gradient(125deg, var(--sheen-dark) 0%, var(--sheen-mid) 35%, var(--sheen-light) 55%, var(--sheen-mid) 70%, var(--sheen-dark) 100%);
  }
  .back__brand {
    position: absolute; right: 34px; bottom: 30px;
    display: flex; align-items: center; gap: 10px;
  }
  .back__mark { width: 22px; height: 22px; background: var(--red); }
  .back__name { color: var(--red); font-weight: 800; font-size: 24px; letter-spacing: -.5px; }
</style>
</head>
<body>
  <div class="card card--front">
    <div class="brand">
      <span class="brand__mark"></span>
      <span class="brand__name">Brindovalle.com</span>
    </div>

    <div class="person">
      <div class="person__name">Marlo Venter</div>
      <div class="person__title">Director</div>
    </div>

    <div class="divider"></div>

    <ul class="contact">
      <li class="contact__address">2841 W Harlow Rd, Dunmore,<br>Ohio 43920</li>
      <li class="contact__item">
        <svg class="contact__icon" viewBox="0 0 16 16"><path fill="#e8232e" d="M4 1l2.5 3.5-1.5 2c.8 1.8 2.4 3.4 4.2 4.2l2-1.5L15 11.7 13 15C6.5 14.5 1.5 9.5 1 3z"/></svg>
        555-214-0387
      </li>
      <li class="contact__item">
        <svg class="contact__icon" viewBox="0 0 16 16"><rect x="1" y="3" width="14" height="10" fill="#e8232e"/><path d="M1.5 3.5L8 9l6.5-5.5" fill="none" stroke="#19191b" stroke-width="1.5"/></svg>
        info@brindovalle.com
      </li>
      <li class="contact__item">
        <svg class="contact__icon" viewBox="0 0 16 16"><circle cx="8" cy="8" r="7" fill="#e8232e"/></svg>
        brindovalle
      </li>
    </ul>

    <div class="card__band"></div>
  </div>

  <div class="card card--back">
    <div class="back__pattern" role="img" aria-label="Repeating glossy black brand-mark pattern across the card back"></div>
    <div class="back__brand">
      <span class="back__mark"></span>
      <span class="back__name">Brindovalle</span>
    </div>
  </div>
</body>
</html>
```